Brindlewood Home & Commercial Services, Inc.

I need a facebook design for our commercial repair/maintenance company based in Austin, TX. We offer many commercial services:plumbing, HVAC, Carpet/Air duct cleaning, Fire and water restoration, and general maintenance services
Our customer base includes commercial government organizations as NMDX and Fort Tellison. We serve as the general contractor for these organizations and can handle any scope of work. ie flooring install, drywall, asbestos abatement, and mold removal.
We need a facebook design that communicates to our customer that we strive in customer satisfaction and pricing.
Updates
Logo uploaded. I will also upload photos for some job that have been completed.
I don't have images of our employees actively doing a job. I do have before and after picture that intend to post after fb cover is created.
I like the designs. I will sit with my husband tonight to brainstorm or select a design. Keep submitting, please.
Target Market(s)
Commercial
Industry/Entity Type
Government
Look and feel

```html
<!DOCTYPE html>
<html lang="en">
<head>
<meta charset="utf-8">
<title>Brindlewood Home &amp; Commercial Services – Cover</title>
<link rel="stylesheet" href="https://fonts.googleapis.com/css2?family=Gelasio:wght@400&display=swap">
<style>
  :root {
    --paper: #ffffff;
    --sky: #7aaed6;
    --steel: #4f8ec4;
    --ocean: #2f6aa6;
    --navy: #1c3f72;
    --badge: #2a5f9e;
  }
  html, body {
    margin: 0;
    padding: 0;
    width: 1200px;
    height: 444px;
    overflow: hidden;
    background: var(--paper);
  }
  .cover {
    display: block;
    width: 1200px;
    height: 444px;
  }
  .word {
    font-family: "Gelasio", Georgia, serif;
    font-weight: 400;
  }
  .tone-sky { fill: var(--sky); }
  .tone-steel { fill: var(--steel); }
  .tone-ocean { fill: var(--ocean); }
  .tone-navy { fill: var(--navy); }
  .brand-name {
    font-family: "Gelasio", Georgia, serif;
    font-weight: 400;
    fill: var(--navy);
  }
  .brand-mark { fill: var(--navy); }
  .listing-badge { fill: var(--badge); }
</style>
</head>
<body>
<svg class="cover" viewBox="0 0 1200 444" xmlns="http://www.w3.org/2000/svg" role="img" aria-label="Word cloud of Brindlewood services">
  <g class="word-cloud">
    <text class="word tone-sky" x="423" y="56" font-size="42" textLength="212" lengthAdjust="spacingAndGlyphs">contractor</text>
    <text class="word tone-sky" x="532" y="96" font-size="42" textLength="222" lengthAdjust="spacingAndGlyphs">restoration</text>
    <text class="word tone-ocean" x="818" y="82" font-size="40" textLength="118" lengthAdjust="spacingAndGlyphs">water</text>
    <text class="word tone-steel" x="705" y="120" font-size="37" textLength="262" lengthAdjust="spacingAndGlyphs">maintenance</text>

    <text class="word tone-sky" x="18" y="160" font-size="160" textLength="405" lengthAdjust="spacingAndGlyphs">repair</text>
    <text class="word tone-navy" x="454" y="154" font-size="45" textLength="204" lengthAdjust="spacingAndGlyphs">plumbing</text>
    <text class="word tone-sky" x="677" y="168" font-size="92" textLength="455" lengthAdjust="spacingAndGlyphs">guaranteed</text>

    <text class="word tone-navy" x="491" y="198" font-size="43" textLength="174" lengthAdjust="spacingAndGlyphs">cleaning</text>
    <text class="word tone-steel" x="740" y="200" font-size="43" textLength="108" lengthAdjust="spacingAndGlyphs">mold</text>
    <text class="word tone-ocean" x="963" y="205" font-size="43" textLength="110" lengthAdjust="spacingAndGlyphs">ducts</text>

    <text class="word tone-navy" x="225" y="215" font-size="40" textLength="58" lengthAdjust="spacingAndGlyphs">air</text>
    <text class="word tone-ocean" x="296" y="238" font-size="41" textLength="163" lengthAdjust="spacingAndGlyphs">flooring</text>
    <text class="word tone-sky" x="183" y="270" font-size="37" textLength="170" lengthAdjust="spacingAndGlyphs">asbestos</text>
    <text class="word tone-sky" x="414" y="298" font-size="38" textLength="128" lengthAdjust="spacingAndGlyphs">HVAC</text>

    <text class="word tone-ocean" x="578" y="303" font-size="156" textLength="602" lengthAdjust="spacingAndGlyphs">services</text>
    <text class="word tone-navy" x="630" y="345" font-size="40" textLength="258" lengthAdjust="spacingAndGlyphs">construction</text>
  </g>

  <g class="brand">
    <rect class="brand-mark" x="282" y="338" width="26" height="26"/>
    <text class="brand-name" x="318" y="362" font-size="34" textLength="262" lengthAdjust="spacingAndGlyphs">Brindlewood</text>
    <text class="brand-name" x="282" y="396" font-size="17" textLength="298" lengthAdjust="spacingAndGlyphs">Home &amp; Commercial Services</text>
  </g>

  <rect class="listing-badge" x="622" y="372" width="20" height="48" rx="2"/>
</svg>
</body>
</html>
```